Quill Press Oceania needs a website

We require a website design which will be different to the normal websites that you visit. The objective of this website will be a call to action on the last page which will link to our email address so customers can email us their quotation requirements.

An example of how we envisage the look and the pages turning is as a flip books for example: https://www.vidharbor.example/watch?v=KtLmPzQa7Rw&feature=vh.be

page 1: just has our logo on it with the tag "Specialist producing quality printed books to your deadline."

Page 2: Black Page with white text "Black and White Book"
These are produced either digitally or offset on a complete range of stocks

Page 3: Colour books (use an image of your choice) These are also produced either digitally or offset plus we have the choice of web presses for larger print runs

Page 4: Digital books We do have a minimum run of 50 books using this process so a one off Thesis is not economically viable using this process. In special circumstance the digital process can produce books more quickly then by using our offset printing process.

Page 5: Having the complete range of printing machines at our disposal enables you to make a perfectly informed choice for your special project.

Then we need a special quote button which takes them directly to our email link. On this page we also need to add: We have had 25 years' experience printing books saving customers time and money whilst guaranteeing quality

Page 6: Logo repeated from page one with name: Morgan Elsworth and mobile phone no 0487 552 314

- Must follow the brief exactly. Must have a turn page book. Clear, simple and concise with a touch of creative flare and must lead into a call for action which is there quotation. A unique button for quotation link...something out of the ordinary which makes someone want to get a quote.

- It would be nice to have 3D Logo on Page 1 & 6.
a unique button for quotation link...something that make someone eager to proceed.

Our main objective is that they should not leave our website without giving us a quote. Please make sure that the spelling is correct and we do not require clip art images. Continue the logo colours through the theme
Updates

here is another example www.vidharbor.example/watch?v=JbXo412TrGe Added Saturday, May 13, 2017

Target Market(s)

Schools, Universities, Self Publishers, Publishers, Graphic Designers, Conference Providers, Businesses, Corporations, Government.

Industry/Entity Type

Printing

Coding

Coded - Design and coding required

Number of Pages Required

5+ page

Font styles to use
Sans Serif

Colors
34a6d7
ec1f27
fbed22
9bcb3c
ffc214
6b449b

Requirements
Must have
• Must follow the brief exactly. Must have a turn page book. Clear, simple and concise with a touch of creative flare and must lead into a call for action which is there quotation. A unique button for quotation link...something out of the ordinary which makes someone want to get a quote. would like to see the colours of the logo use throughout
Nice to have
• 3D Logo on Page 1 & 6.
• a unique button for quotation link...something that make someone eager to proceed.
• Our main objective is that they should not leave our website without giving us a quote
Should not have
• Spelling mistakes, clip art, ordinary design

```html
<!DOCTYPE html>
<html lang="en">
<head>
<meta charset="utf-8">
<title>Quill Press Oceania – Digital Books</title>
<link href="https://fonts.googleapis.com/css2?family=Mulish:wght@400;500&display=swap" rel="stylesheet">
<style>
  :root {
    --sun: #fdd445;
    --orange: #f68a22;
    --green: #62a944;
    --blue: #12679d;
    --ribbon: #e83509;
    --ribbon-tail: #f3612a;
    --ink: #2b2620;
    --paper: #ffffff;
    --muted: #6c6455;
    --art-red: #ee4b3f;
    --art-sky: #29a9dc;
    --art-amber: #f09a2a;
    --art-leaf: #8dbd3a;
    --art-slate: #8e93a3;
  }
  * { margin: 0; padding: 0; box-sizing: border-box; }
  html, body { width: 720px; height: 1200px; overflow: hidden; background: var(--sun); }
  .page {
    position: relative;
    width: 720px;
    height: 1200px;
    overflow: hidden;
    background: var(--sun);
    font-family: "Mulish", sans-serif;
    color: var(--ink);
  }
  .decor { position: absolute; inset: 0; width: 720px; height: 1200px; }
  .hero-glow {
    position: absolute;
    left: 96px; top: 120px;
    width: 476px; height: 420px;
    background: radial-gradient(ellipse at 52% 45%, #fff6c8 0%, #fbe47e 35%, rgba(253,212,69,0) 70%);
  }
  .hero-art {
    position: absolute;
    left: 170px; top: 140px;
    width: 400px; height: 380px;
    border-radius: 28px;
    background: linear-gradient(170deg,
      var(--art-red) 0%,
      var(--art-red) 18%,
      var(--art-sky) 34%,
      var(--art-sky) 46%,
      var(--art-amber) 58%,
      var(--art-leaf) 74%,
      var(--art-slate) 100%);
    opacity: 0.85;
  }
  .ribbon {
    position: absolute;
    left: 168px; top: 541px;
    width: 406px; height: 45px;
  }
  .ribbon svg { position: absolute; inset: 0; }
  .ribbon-label {
    position: absolute; inset: 0;
    display: flex; align-items: center; justify-content: center;
    color: var(--paper);
    font-size: 19px;
    font-weight: 500;
    letter-spacing: 0.3px;
    padding-bottom: 4px;
  }
  .copy {
    position: absolute;
    left: 104px; top: 622px;
    width: 520px;
    text-align: center;
    font-size: 23.5px;
    line-height: 45px;
  }
  .copy p + p { margin-top: 19px; }
  .brand {
    position: absolute;
    left: 20px; top: 1048px;
    width: 200px;
    text-align: center;
    color: #1c1c1c;
    font-weight: 500;
  }
  .brand-name { font-size: 27px; line-height: 32px; }
  .brand-region { font-size: 18px; line-height: 24px; }
  .page-code {
    position: absolute;
    left: 683px; top: 1170px;
    font-size: 13px;
    color: var(--muted);
  }
</style>
</head>
<body>
<main class="page">
  <svg class="decor" viewBox="0 0 720 1200" aria-hidden="true">
    <rect class="tile tile-orange" x="635" y="-21" width="170" height="170" rx="12" transform="rotate(45 720 64)" fill="var(--orange)"/>
    <rect class="tile tile-green" x="544" y="60" width="96" height="96" rx="8" transform="rotate(45 592 108)" fill="var(--green)"/>
    <rect class="tile tile-blue" x="612" y="132" width="96" height="96" rx="8" transform="rotate(45 660 180)" fill="var(--blue)"/>
    <path class="panel-white" d="M0 804 Q10 800 22 810 L240 1030 Q262 1054 240 1078 L118 1200 L0 1200 Z" fill="var(--paper)"/>
    <rect class="tile tile-green" x="148" y="1160" width="96" height="96" rx="8" transform="rotate(45 196 1208)" fill="var(--green)"/>
    <rect class="tile tile-blue" x="224" y="1092" width="96" height="96" rx="8" transform="rotate(45 272 1140)" fill="var(--blue)"/>
  </svg>

  <div class="hero-glow" aria-hidden="true"></div>
  <div class="hero-art" role="img" aria-label="Stack of colourful books rising from a tablet with clouds behind"></div>

  <div class="ribbon">
    <svg viewBox="0 0 406 45" aria-hidden="true">
      <polygon points="0,6 40,6 40,45 0,45 12,25" fill="var(--ribbon-tail)"/>
      <polygon points="406,6 366,6 366,45 406,45 394,25" fill="var(--ribbon-tail)"/>
      <rect x="22" y="0" width="362" height="38" fill="var(--ribbon)"/>
    </svg>
    <span class="ribbon-label">DIGITAL BOOKS</span>
  </div>

  <section class="copy">
    <p>Digital books We do have a minimum run of 50 books using this process so a one off Thesis is not economically viable using this process.</p>
    <p>In special circumstance the digital process can produce books more quickly then by using our offset printing process.</p>
  </section>

  <div class="brand">
    <div class="brand-name">Quill Press</div>
    <div class="brand-region">Oceania</div>
  </div>

  <span class="page-code">C6</span>
</main>
</body>
</html>
```